Need Business Card for our Real Estate Business with Sales Executive's Picture

PANTONE 484 C ( RED)

PANTONE 2766 C ( BLUE

Industry/Entity Type

Real Estate

Contact Information for Business Card

Name, Mobile, email, & picture of Person
Agency Phone, address, Web address

Requirements
Must have
• Our Logo Colours, Agent Picture,

```html
<!DOCTYPE html>
<html lang="en">
<head>
<meta charset="utf-8">
<title>Mesa Ridge Realty – Business Card</title>
<link rel="stylesheet" href="https://fonts.googleapis.com/css2?family=Arima:wght@600&family=Open+Sans:wght@400&display=swap">
<style>
  :root {
    --navy: #1b2a5a;
    --red: #a8312b;
    --card: #f7f5f2;
    --page: #e6e4e1;
    --ink: #26304f;
    --photo-top: #d9d2c8;
    --photo-bottom: #2a3b6b;
    --web-text: #d9dcea;
  }
  * { margin: 0; padding: 0; box-sizing: border-box; }
  html, body { width: 1200px; height: 1054px; overflow: hidden; }
  body { background: var(--page); position: relative; font-family: "Open Sans", sans-serif; }

  .business-card {
    position: absolute; left: 100px; top: 227px;
    width: 1000px; height: 600px;
    background: var(--card);
    overflow: hidden;
    box-shadow: 0 10px 30px rgba(0,0,0,0.12);
  }

  .brand {
    position: absolute; left: 48px; top: 196px;
    display: flex; align-items: center; gap: 12px;
  }
  .brand-square { width: 14px; height: 14px; background: var(--red); }
  .brand-name {
    font-family: "Arima", serif; font-weight: 600;
    font-size: 40px; color: var(--navy); letter-spacing: 1px;
  }

  .agent-photo {
    position: absolute; left: 641px; top: 38px;
    width: 359px; height: 367px;
    background: linear-gradient(180deg, var(--photo-top) 0%, #c9b8a6 55%, var(--photo-bottom) 100%);
  }

  .agent-name {
    position: absolute; left: 48px; top: 338px;
    font-family: "Arima", serif; font-weight: 600;
    font-size: 36px; color: var(--navy);
  }
  .agent-title {
    position: absolute; left: 48px; top: 384px;
    font-size: 23px; color: var(--red);
  }
  .title-rule {
    position: absolute; left: 283px; top: 403px;
    width: 717px; height: 3px; background: var(--red);
  }

  .contact-list {
    position: absolute; left: 48px; top: 440px;
    list-style: none;
  }
  .contact-list li {
    display: flex; align-items: center; gap: 12px;
    height: 33px; font-size: 23px; color: var(--ink);
  }
  .contact-list svg { width: 22px; height: 22px; fill: var(--red); flex-shrink: 0; }

  .office-address {
    position: absolute; left: 620px; top: 448px;
    font-size: 23px; line-height: 33px; color: var(--ink);
    font-style: normal;
  }

  .stripe-navy { position: absolute; left: 0; top: 577px; width: 540px; height: 8px; background: var(--navy); }
  .stripe-red { position: absolute; left: 0; top: 592px; width: 530px; height: 8px; background: var(--red); }

  .web-tab { position: absolute; left: 540px; top: 542px; width: 460px; height: 58px; }
  .web-address {
    position: absolute; left: 620px; top: 542px; height: 58px;
    display: flex; align-items: center;
    font-size: 23px; color: var(--web-text);
  }
</style>
</head>
<body>
  <div class="business-card">
    <div class="brand">
      <span class="brand-square"></span>
      <span class="brand-name">MESA RIDGE REALTY</span>
    </div>

    <div class="agent-photo" role="img" aria-label="Portrait photo of the sales agent in a navy suit"></div>

    <h1 class="agent-name">Marissa Holloway</h1>
    <p class="agent-title">Managing Director</p>
    <div class="title-rule"></div>

    <ul class="contact-list">
      <li>
        <svg viewBox="0 0 24 24" aria-hidden="true"><path d="M7 1h10a2 2 0 0 1 2 2v18a2 2 0 0 1-2 2H7a2 2 0 0 1-2-2V3a2 2 0 0 1 2-2zm0 3v14h10V4H7zm5 15.5a1.2 1.2 0 1 0 0 2.4 1.2 1.2 0 0 0 0-2.4z"/></svg>
        <span>555.214.7730</span>
      </li>
      <li>
        <svg viewBox="0 0 24 24" aria-hidden="true"><path d="M6.6 10.8a15.1 15.1 0 0 0 6.6 6.6l2.2-2.2a1 1 0 0 1 1-.25 11.4 11.4 0 0 0 3.6.57 1 1 0 0 1 1 1V20a1 1 0 0 1-1 1A17 17 0 0 1 3 4a1 1 0 0 1 1-1h3.5a1 1 0 0 1 1 1c0 1.25.2 2.45.57 3.57a1 1 0 0 1-.25 1z"/></svg>
        <span>555-908-3461</span>
      </li>
      <li>
        <svg viewBox="0 0 24 24" aria-hidden="true"><path d="M2 5h20v14H2V5zm2 2v.5l8 5 8-5V7H4zm0 2.8V17h16V9.8l-8 5-8-5z"/></svg>
        <span>mholloway@mesaridgerealty.com</span>
      </li>
    </ul>

    <address class="office-address">418 Aspen Court #210,<br>Fairview, CO 80412</address>

    <div class="stripe-navy"></div>
    <div class="stripe-red"></div>

    <svg class="web-tab" viewBox="0 0 460 58" aria-hidden="true">
      <path d="M0 58 L22 14 Q29 0 45 0 L460 0 L460 58 Z" fill="var(--navy)"/>
    </svg>
    <p class="web-address">www.mesaridgerealty.com</p>
  </div>
</body>
</html>
```